Road Construction Company needs business cards

We would like a new business card designed for our business.

We're a road construction company based in Qld, Australia.

Can the business card please have the following information on it.

Name: Warren Halbeck
Position: General Manager
Phone: 0472 915 348
Email: Warren.halbeck@tovrin.com.au
Address: 87 Marrow Ave, Pendlebay, QLD, 4023
Website: www.tovrin.com.au

Visually we'd like the card to be professional and simple.

Attached is our logo.

Our website is www.tovrin.com.au

Target Market(s)

Men aged 25-60

Contact Information for Business Card

As listed in project description

Font styles to use
Serif

Requirements
Must have
• Large logo on back of card

```html
<!DOCTYPE html>
<html lang="en">
<head>
<meta charset="utf-8">
<title>Tovrin Business Card</title>
<link href="https://fonts.googleapis.com/css2?family=Poppins:wght@400;500;700&display=swap" rel="stylesheet">
<style>
  :root {
    --backdrop: #0e0e0f;
    --card: #2a2b2e;
    --card-back: #262729;
    --edge: #1560c4;
    --brand-blue: #1a6fd6;
    --text-light: #e6e7e9;
    --rule: #55575c;
    --emboss: #6d6f74;
  }
  * { margin: 0; padding: 0; box-sizing: border-box; }
  html, body {
    width: 1200px; height: 820px; overflow: hidden;
    background: var(--backdrop);
    font-family: "Poppins", sans-serif;
  }
  .canvas {
    position: relative; width: 1200px; height: 820px;
  }
  .card {
    position: absolute; top: 245px;
    width: 540px; height: 330px;
    border-left: 4px solid var(--edge);
    border-bottom: 4px solid var(--edge);
    border-radius: 3px;
  }
  .card-front { left: 45px; background: var(--card); }
  .card-back { left: 615px; background: var(--card-back); }

  .front-brand {
    position: absolute; left: 220px; top: 58px;
    font-weight: 700; font-size: 50px; letter-spacing: 3px;
    color: var(--brand-blue); line-height: 1;
  }
  .divider {
    position: absolute; left: 40px; right: 40px; top: 170px;
    height: 1px; background: var(--rule);
  }
  .person {
    position: absolute; left: 40px; top: 112px;
  }
  .person-name {
    font-weight: 500; font-size: 22px; color: var(--brand-blue);
    text-transform: uppercase; line-height: 1.1;
  }
  .person-role {
    font-size: 15px; color: var(--text-light); margin-top: 2px;
  }
  .contacts {
    position: absolute; left: 40px; top: 192px;
    list-style: none;
  }
  .contacts li {
    display: flex; align-items: center; gap: 8px;
    font-size: 14px; color: var(--text-light); line-height: 1.6;
  }
  .contacts svg { width: 13px; height: 13px; flex: none; }
  .address {
    position: absolute; right: 40px; top: 192px;
    font-size: 14px; color: var(--text-light); line-height: 1.6;
    text-align: left;
  }
  .back-brand {
    position: absolute; left: 0; right: 0; top: 135px;
    text-align: center;
    font-weight: 700; font-size: 56px; letter-spacing: 4px;
    color: var(--emboss); line-height: 1;
  }
</style>
</head>
<body>
<main class="canvas">
  <section class="card card-front" aria-label="Card front">
    <div class="front-brand">TOVRIN</div>
    <div class="person">
      <p class="person-name">Warren Halbeck</p>
      <p class="person-role">General Manager</p>
    </div>
    <div class="divider"></div>
    <ul class="contacts">
      <li>
        <svg viewBox="0 0 24 24" aria-hidden="true"><path fill="var(--brand-blue)" d="M6.6 10.8a15 15 0 0 0 6.6 6.6l2.2-2.2c.3-.3.7-.4 1-.2 1.1.4 2.3.6 3.6.6.6 0 1 .4 1 1V20c0 .6-.4 1-1 1A17 17 0 0 1 3 4c0-.6.4-1 1-1h3.5c.6 0 1 .4 1 1 0 1.3.2 2.5.6 3.6.1.3 0 .7-.2 1z"/></svg>
        0472 915 348
      </li>
      <li>
        <svg viewBox="0 0 24 24" aria-hidden="true"><path fill="var(--brand-blue)" d="M2 5h20v14H2z"/><path fill="none" stroke="var(--card)" stroke-width="1.8" d="M2 5l10 8 10-8"/></svg>
        Warren.halbeck@tovrin.com.au
      </li>
      <li>
        <svg viewBox="0 0 24 24" aria-hidden="true"><g fill="none" stroke="var(--brand-blue)" stroke-width="2"><circle cx="12" cy="12" r="9"/><ellipse cx="12" cy="12" rx="4" ry="9"/><path d="M3 12h18"/></g></svg>
        www.tovrin.com.au
      </li>
    </ul>
    <p class="address">87 Marrow Ave<br>Pendlebay, QLD, 4023</p>
  </section>

  <section class="card card-back" aria-label="Card back">
    <div class="back-brand">TOVRIN</div>
  </section>
</main>
</body>
</html>
```